business card deign

Logo needs the following on it.
1. attached logo
2. Tagline - "From Chilled Cans To Late Nights...We Bring The Fun!"
3. Name- Dalton Pikes, Founder and CPO
4. Address - 412 E. Carver Avenue, Ste 2207, Tampa, FL. 33917
5. Phone - 555.318.4726

```html
<!DOCTYPE html>
<html lang="en">
<head>
<meta charset="utf-8">
<title>Hoppa Business Card</title>
<link href="https://fonts.googleapis.com/css2?family=Jost:wght@400;500;600;700&display=swap" rel="stylesheet">
<style>
  :root {
    --backdrop: #4a4a4c;
    --card: #f7f7f7;
    --ink: #111111;
    --muted: #555555;
    --band: #0b0b0b;
    --gold: #c9a24a;
    --gold-light: #e8c978;
  }
  * { margin: 0; padding: 0; box-sizing: border-box; }
  html, body {
    width: 1200px; height: 900px; overflow: hidden;
    background: var(--backdrop);
    font-family: "Jost", sans-serif;
  }
  .stage { position: relative; width: 1200px; height: 900px; }
  .card {
    position: absolute;
    width: 600px; height: 343px;
    background: var(--card);
    box-shadow: 0 12px 30px rgba(0,0,0,0.35);
    overflow: hidden;
  }
  .card-front { left: 90px; top: 70px; }
  .card-back { left: 510px; top: 487px; }

  .wordmark {
    color: var(--ink);
    font-weight: 600;
    letter-spacing: 0.32em;
    text-transform: uppercase;
  }
  .card-front .wordmark {
    position: absolute; left: 0; right: 0; top: 140px;
    text-align: center; font-size: 54px; padding-left: 0.32em;
  }
  .card-back .wordmark {
    position: absolute; right: 40px; top: 70px;
    font-size: 36px;
  }

  .contact { position: absolute; left: 42px; top: 108px; color: var(--muted); }
  .contact-name { color: var(--ink); font-weight: 700; font-size: 21px; letter-spacing: 0.02em; text-transform: uppercase; }
  .contact-role { font-size: 16px; margin-bottom: 14px; }
  .contact-line { font-size: 15px; line-height: 1.35; display: flex; align-items: center; gap: 6px; }
  .contact-line svg { width: 14px; height: 14px; fill: var(--ink); }

  .band { position: absolute; left: 0; top: 0; width: 600px; height: 343px; }
  .tagline {
    position: absolute; left: 0; right: 0; bottom: 18px;
    text-align: center; font-weight: 600; font-size: 18px;
    color: var(--gold-light); letter-spacing: 0.02em;
  }
</style>
</head>
<body>
<div class="stage">
  <section class="card card-front">
    <div class="wordmark">Hoppa</div>
  </section>

  <section class="card card-back">
    <svg class="band" viewBox="0 0 600 343" aria-hidden="true">
      <path d="M0,274 L390,274 C404,274 408,268 411,256 L415,236 C418,224 424,219 438,219 L600,219"
            fill="none" stroke="var(--gold)" stroke-width="3"/>
      <path d="M0,281 L394,281 C410,281 414,274 417,262 L421,242 C424,230 430,226 444,226 L600,226 V343 H0 Z"
            fill="var(--band)"/>
    </svg>
    <div class="wordmark">Hoppa</div>
    <div class="contact">
      <div class="contact-name">Dalton Pikes</div>
      <div class="contact-role">Founder and CPO</div>
      <div class="contact-line">
        <svg viewBox="0 0 24 24"><path d="M6.6 10.8a15.1 15.1 0 0 0 6.6 6.6l2.2-2.2a1 1 0 0 1 1-.25 11.4 11.4 0 0 0 3.6.57 1 1 0 0 1 1 1V20a1 1 0 0 1-1 1A17 17 0 0 1 3 4a1 1 0 0 1 1-1h3.5a1 1 0 0 1 1 1c0 1.25.2 2.45.57 3.6a1 1 0 0 1-.25 1z"/></svg>
        555.318.4726
      </div>
      <div class="contact-line">412 E. Carver Avenue</div>
      <div class="contact-line">Ste 2207, Tampa, FL. 33917</div>
    </div>
    <p class="tagline">From Chilled Cans To Late Nights...We Bring The Fun!</p>
  </section>
</div>
</body>
</html>
```